Certificates with Watermark Images

We are looking for a design of One page Certificates with Watermark (background) images where text will be printed over it .
Graphics design is required to reflect the flowing categories:
IPTV (Internet Protocol TV)
VoD (Video on Demand)
Satellite Receiver
Graphics design images for all three categories must be provided to maintain the same them .
Thank you and good luck.
Industry/Entity Type
Internet
Requirements
Must have
- Graphics design images for all three categories must be provided to maintain the same them

```html
<!DOCTYPE html>
<html lang="en">
<head>
<meta charset="utf-8">
<title>Certificate – Satellite Service</title>
<link href="https://fonts.googleapis.com/css2?family=Fira+Sans:ital,wght@0,400;0,500;0,700;1,500;1,700&display=swap" rel="stylesheet">
<style>
  :root {
    --page: #ffffff;
    --sky-light: #f2f8fc;
    --sky-mid: #d9ecf7;
    --sky-deep: #a9d3ec;
    --ink: #1f1f24;
    --accent: #1b9be0;
    --org-dot: #e5462a;
    --seal: #2a10a8;
    --signature: #3a2cae;
    --disc-edge: #b9dcef;
    --disc-fill: #cfe7f5;
    --disc-glow: #e6f3fb;
  }
  * { box-sizing: border-box; margin: 0; padding: 0; }
  html, body {
    width: 1200px; height: 845px; overflow: hidden;
    background: var(--page);
    font-family: "Fira Sans", Arial, sans-serif;
    color: var(--ink);
  }
  .certificate {
    position: absolute; left: 32px; top: 29px;
    width: 1140px; height: 788px;
    border-radius: 48px; overflow: hidden;
    background: linear-gradient(120deg, var(--sky-light) 0%, var(--sky-mid) 55%, var(--sky-deep) 100%);
  }
  .light-streaks {
    position: absolute; inset: 0;
    background:
      radial-gradient(ellipse 420px 120px at 330px 420px, rgba(255,255,255,.85), rgba(255,255,255,0) 70%),
      radial-gradient(ellipse 700px 60px at 450px 300px, rgba(255,255,255,.55), rgba(255,255,255,0) 70%),
      radial-gradient(ellipse 300px 380px at 250px 520px, rgba(170,210,235,.35), rgba(170,210,235,0) 70%);
  }
  .service-emblem {
    position: absolute; left: 663px; top: 160px;
    width: 486px; height: 486px; border-radius: 50%;
    border: 16px solid rgba(185,220,239,.6);
    background: radial-gradient(circle at 45% 40%, var(--disc-glow) 0%, var(--disc-fill) 70%);
    opacity: .9;
  }
  .content {
    position: absolute; left: 79px; top: 0; width: 470px;
    text-align: center;
  }
  .org-mark {
    position: absolute; left: 205px; top: 84px;
    width: 60px; height: 60px; border-radius: 50%;
    background: var(--org-dot); opacity: .85;
  }
  .org-name {
    position: absolute; top: 151px; left: 0; width: 100%;
    font-size: 24px; font-weight: 500;
  }
  .title {
    position: absolute; top: 212px; left: 0; width: 100%;
    font-size: 41px; font-weight: 700; letter-spacing: 6px;
  }
  .lead {
    position: absolute; top: 275px; left: 0; width: 100%;
    font-size: 22px;
  }
  .recipient {
    position: absolute; top: 307px; left: 0; width: 100%;
    font-size: 41px; font-weight: 500; color: var(--accent);
  }
  .service {
    position: absolute; top: 372px; left: 0; width: 100%;
    font-size: 19px;
  }
  .citation {
    position: absolute; top: 418px; left: 30px; width: 410px;
    font-size: 18px; line-height: 23px;
  }
  .fee {
    position: absolute; top: 528px; left: 0; width: 100%;
    font-size: 19px; font-weight: 700;
  }
  .details {
    position: absolute; left: 73px; top: 631px;
    font-size: 13px; font-weight: 700; font-style: italic; line-height: 16px;
  }
  .details .gap { margin-top: 20px; }
  .signature {
    position: absolute; left: 275px; top: 650px;
    width: 82px; height: 76px; border-radius: 40%;
    background: var(--signature); opacity: .18;
  }
  .seal { position: absolute; left: 458px; top: 610px; width: 136px; height: 136px; }
</style>
</head>
<body>
  <main class="certificate">
    <div class="light-streaks" role="img" aria-label="Soft blue background with flowing light streaks"></div>

    <div class="service-emblem" role="img" aria-label="Large faint disc holding the satellite service illustration"></div>

    <section class="content">
      <span class="org-mark" aria-hidden="true"></span>
      <div class="org-name">Our Organization</div>
      <h1 class="title">CERTIFICATE</h1>
      <p class="lead">this certificate that</p>
      <h2 class="recipient">Harbor Vista</h2>
      <p class="service">(satellite service)</p>
      <p class="citation">has been awarded for his labor achievements and many years of diligent work, also for his labor achievements and many years of diligent work.</p>
      <p class="fee">and has passed for this Certificate $100</p>
    </section>

    <div class="details">
      <p>Certificate No. 0000/1</p>
      <p class="gap">11 November 2011</p>
      <p>New-York</p>
      <p class="gap">Our company Genera Director</p>
      <p>Samir Haddad</p>
    </div>

    <div class="signature" role="img" aria-label="Handwritten signature of the director"></div>

    <svg class="seal" viewBox="-68 -68 136 136" aria-hidden="true">
      <polygon fill="var(--seal)" points="
        0,-66 7,-56 18,-63 22,-52 34,-56 35,-44 47,-45 44,-33 56,-31 50,-20 61,-15 53,-6 62,1 53,8 60,16 49,21 54,32 42,34 44,46 32,45 30,57 20,51 14,62 5,53 -2,63 -9,53 -17,61 -22,50 -33,55 -35,43 -47,45 -45,33 -57,30 -50,20 -61,14 -53,5 -62,-2 -53,-9 -60,-17 -49,-22 -54,-33 -42,-35 -43,-47 -31,-45 -28,-57 -18,-50 -11,-61 -4,-53"/>
    </svg>
  </main>
</body>
</html>
```